Ridgeline Journeys business card

please see website
www.ridgelinejourneys.comau

info needed on card
Curtis Halvey
Ph
email
Adventure Riding GPS trails

please use my logo and colours off my site

Curtis Halvey
curtis@ridgelinejourneys.com

```html
<!DOCTYPE html>
<html lang="en">
<head>
<meta charset="utf-8">
<title>Ridgeline Journeys – Business Card</title>
<link href="https://fonts.googleapis.com/css2?family=Open+Sans:wght@300;400;800&display=swap" rel="stylesheet">
<style>
  :root {
    --canvas: #e8e5df;
    --card-white: #ffffff;
    --charcoal: #2b2b2b;
    --accent-yellow: #f4e83c;
    --ink: #1c1c1c;
    --mark-grey: #7a7a7a;
    --light-text: #f2f2f2;
  }
  * { margin: 0; padding: 0; box-sizing: border-box; }
  html, body {
    width: 1200px; height: 858px; overflow: hidden;
    background: var(--canvas);
    font-family: "Open Sans", Arial, sans-serif;
  }
  .canvas { position: relative; width: 1200px; height: 858px; }
  .card {
    position: absolute; top: 269px;
    width: 560px; height: 320px;
    background: var(--card-white);
    box-shadow: 0 6px 18px rgba(0,0,0,0.18);
    overflow: hidden;
  }
  .card--front { left: 27px; }
  .card--back { left: 613px; }
  .card__band { position: absolute; inset: 0; width: 100%; height: 100%; }

  .brand { position: absolute; display: flex; align-items: center; gap: 22px; }
  .brand__dot { width: 74px; height: 74px; border-radius: 50%; background: var(--accent-yellow); flex: none; }
  .brand__name {
    font-weight: 800; text-transform: uppercase; color: var(--ink);
    font-size: 38px; line-height: 1.02; letter-spacing: 0.5px;
  }
  .card--front .brand { left: 46px; top: 36px; }
  .card--back .brand { left: 50%; top: 50%; transform: translate(-50%, -50%); }
  .card--back .brand__name { font-size: 42px; }

  .holder {
    position: absolute; left: 32px; top: 238px;
    font-weight: 300; font-size: 27px; color: var(--light-text);
  }
  .divider {
    position: absolute; left: 228px; top: 214px;
    width: 1px; height: 80px; background: var(--light-text);
  }
  .contact { position: absolute; left: 244px; top: 214px; list-style: none; }
  .contact__item {
    display: flex; align-items: center; gap: 8px;
    font-size: 15px; color: var(--light-text); line-height: 30px;
  }
  .contact__icon { width: 14px; height: 14px; flex: none; }
</style>
</head>
<body>
<main class="canvas">

  <section class="card card--front" aria-label="Card front">
    <svg class="card__band" viewBox="0 0 560 320" aria-hidden="true">
      <path d="M0,190 C140,190 230,120 380,102 L560,84 L560,320 L0,320 Z" fill="var(--accent-yellow)"/>
      <path d="M0,202 C140,202 230,132 380,114 L560,96 L560,320 L0,320 Z" fill="var(--charcoal)"/>
    </svg>
    <div class="brand">
      <span class="brand__dot"></span>
      <span class="brand__name">Ridgeline<br>Journeys</span>
    </div>
    <p class="holder">Curtis Halvey</p>
    <span class="divider"></span>
    <ul class="contact">
      <li class="contact__item">
        <svg class="contact__icon" viewBox="0 0 14 14" aria-hidden="true">
          <rect x="0.5" y="2.5" width="13" height="9" fill="none" stroke="currentColor"/>
          <path d="M1,3 L7,8 L13,3" fill="none" stroke="currentColor"/>
        </svg>
        curtis@ridgelinejourneys.com
      </li>
      <li class="contact__item">
        <svg class="contact__icon" viewBox="0 0 14 14" aria-hidden="true">
          <circle cx="7" cy="7" r="6" fill="none" stroke="currentColor"/>
          <ellipse cx="7" cy="7" rx="2.6" ry="6" fill="none" stroke="currentColor"/>
          <path d="M1,7 H13" stroke="currentColor"/>
        </svg>
        www.ridgelinejourneys.comau
      </li>
    </ul>
  </section>

  <section class="card card--back" aria-label="Card back">
    <div class="brand">
      <span class="brand__dot"></span>
      <span class="brand__name">Ridgeline<br>Journeys</span>
    </div>
  </section>

</main>
</body>
</html>
```